Specialised investor in e-mobility and energy wants business card design

We need a business card design that fits our existing corporate design. <The look and feel must be 'sharp'/'clean', dynamic, communicate momentum, professionalism etc (as one would imagine from a firm in the financial sector). We like the idea of a reverse-side of the card that includes the logo, and the name and contact details on the other. We expect the deliverable to be whatever format might be required to be able to get cards printed directly by a service such as kelmo press. Our website is www.zub.capital

```html
<!DOCTYPE html>
<html lang="en">
<head>
<meta charset="utf-8">
<title>ZUB Capital – Business Card</title>
<link rel="stylesheet" href="https://fonts.googleapis.com/css2?family=Montserrat:wght@400;500;700&display=swap">
<style>
  :root {
    --bg: #e9ebe6;
    --forest: #2f5127;
    --forest-deep: #27461f;
    --lime: #7cb342;
    --ink: #151515;
    --paper: #ffffff;
    --text-light: #f2f2f2;
  }
  * { box-sizing: border-box; margin: 0; padding: 0; }
  html, body { width: 1200px; height: 960px; overflow: hidden; }
  body {
    background: var(--bg);
    font-family: "Montserrat", Arial, sans-serif;
    position: relative;
  }
  .card {
    position: absolute;
    left: 320px;
    width: 560px;
    height: 320px;
    border-radius: 24px;
    overflow: hidden;
    box-shadow: 0 10px 28px rgba(0,0,0,0.18);
  }
  .card--back {
    top: 130px;
    background: linear-gradient(135deg, var(--forest) 0%, #3b6230 55%, var(--forest-deep) 100%);
    display: flex;
    align-items: center;
    justify-content: center;
  }
  .wordmark {
    color: var(--paper);
    font-weight: 400;
    font-size: 64px;
    letter-spacing: 1px;
  }
  .card--front { top: 510px; background: var(--ink); }
  .front-art { position: absolute; inset: 0; }
  .front-wordmark {
    position: absolute;
    left: 34px;
    top: 40px;
    color: var(--paper);
    font-weight: 400;
    font-size: 30px;
  }
  .big-mark {
    position: absolute;
    left: 372px;
    top: 96px;
    width: 170px;
    text-align: center;
    color: var(--forest);
    font-weight: 400;
    font-size: 66px;
    letter-spacing: 2px;
  }
  .person { position: absolute; left: 34px; top: 118px; }
  .person__name {
    color: var(--lime);
    font-weight: 700;
    font-size: 20px;
    letter-spacing: 0.5px;
  }
  .person__role { color: var(--text-light); font-size: 14px; margin-top: 3px; }
  .contacts { position: absolute; left: 34px; top: 186px; list-style: none; }
  .contacts li {
    display: flex;
    align-items: center;
    gap: 8px;
    color: var(--text-light);
    font-size: 13px;
    line-height: 21px;
  }
  .contacts svg { width: 12px; height: 12px; fill: var(--lime); flex: none; }
  .office { position: absolute; left: 34px; top: 260px; font-size: 13px; line-height: 19px; }
  .office__company { color: var(--lime); font-weight: 500; }
  .office__city { color: var(--text-light); }
</style>
</head>
<body>

<section class="card card--back" aria-label="Card reverse">
  <div class="wordmark">ZUB Capital</div>
</section>

<section class="card card--front" aria-label="Card front">
  <svg class="front-art" viewBox="0 0 560 320" aria-hidden="true">
    <path d="M395 0 C320 80 330 250 430 320 L560 320 L560 0 Z" fill="var(--forest)"/>
    <path d="M392 0 C322 85 335 245 445 320 L560 320 L560 0 Z" fill="var(--lime)"/>
    <path d="M402 0 C338 88 350 240 470 320 L560 320 L560 0 Z" fill="var(--paper)"/>
    <path d="M404 0 C345 90 360 235 478 320" fill="none" stroke="var(--lime)" stroke-width="5"/>
    <path d="M396 0 C330 86 340 248 452 320" fill="none" stroke="var(--forest)" stroke-width="6"/>
  </svg>

  <div class="front-wordmark">ZUB Capital</div>
  <div class="big-mark">ZUB</div>

  <div class="person">
    <p class="person__name">MARC OBERLIN</p>
    <p class="person__role">Managing Director</p>
  </div>

  <ul class="contacts">
    <li>
      <svg viewBox="0 0 24 24"><path d="M6.6 10.8a15 15 0 0 0 6.6 6.6l2.2-2.2c.3-.3.7-.4 1-.2 1.1.4 2.3.6 3.6.6.6 0 1 .4 1 1V20c0 .6-.4 1-1 1A17 17 0 0 1 3 4c0-.6.4-1 1-1h3.5c.6 0 1 .4 1 1 0 1.3.2 2.5.6 3.6.1.3 0 .7-.2 1z"/></svg>
      +41 79 555 0142
    </li>
    <li>
      <svg viewBox="0 0 24 24"><path d="M2 5h20v14H2z M2 5l10 8 10-8" /></svg>
      marc@zub.capital
    </li>
    <li>
      <svg viewBox="0 0 24 24"><circle cx="12" cy="12" r="10"/></svg>
      www.zub.capital
    </li>
  </ul>

  <div class="office">
    <p class="office__company">ZUB Capital S.A.</p>
    <p class="office__city">Lausanne, Switzerland</p>
  </div>
</section>

</body>
</html>
```